Car transport business

We need a new business card design. Attached is our old card sample. I would just like to adjust the logo colors (blue and red) to be brighter. I changed my name to the brighter red and the word dispatcher to a brighter blue as an example. But you can adjust those colors further. And then perhaps you can use the same colors for the card design but use your imagination.

As a suggestion so the card stands out I would like to add a clip art of car carrier truck. Attached are examples of that as well

```html
<!DOCTYPE html>
<html lang="en">
<head>
<meta charset="utf-8">
<title>Apex Haul – Business Card</title>
<link href="https://fonts.googleapis.com/css2?family=Roboto+Condensed:wght@400;700&display=swap" rel="stylesheet">
<style>
  :root {
    --page: #d9d9d9;
    --card: #262626;
    --card-edge: #1c1c1c;
    --pattern: #2c2c2c;
    --brand-blue: #1e88ff;
    --brand-red: #ff1f2d;
    --silver: #e6e6e6;
    --silver-soft: #bdbdbd;
    --swoosh-light: #5a5a5a;
    --swoosh-dark: #2a2a2a;
  }
  * { margin: 0; padding: 0; box-sizing: border-box; }
  html, body { width: 1200px; height: 874px; overflow: hidden; }
  body {
    background: var(--page);
    font-family: "Roboto Condensed", "Arial Narrow", sans-serif;
    position: relative;
  }
  .card {
    position: absolute;
    left: 340px;
    width: 520px;
    height: 297px;
    background: var(--card);
    border: 1px solid var(--card-edge);
    border-radius: 4px;
    overflow: hidden;
    box-shadow: 0 8px 20px rgba(0,0,0,.25);
  }
  .card--front { top: 120px; }
  .card--back  { top: 457px; }

  /* front */
  .front-pattern {
    position: absolute; inset: 0;
    background: linear-gradient(135deg, var(--pattern), var(--card) 60%, var(--pattern));
  }
  .front-brand {
    position: absolute;
    left: 0; right: 0; top: 108px;
    display: flex; flex-direction: column; align-items: center;
  }
  .brand-row { display: flex; align-items: center; gap: 14px; }
  .brand-dot {
    width: 34px; height: 34px; border-radius: 50%;
    background: var(--brand-blue);
  }
  .brand-name {
    font-weight: 700; font-size: 50px; letter-spacing: 3px;
    line-height: 1; color: var(--brand-red);
    text-transform: uppercase;
  }
  .brand-tagline {
    margin-top: 8px;
    font-size: 13px; letter-spacing: 3.5px;
    color: var(--brand-blue); text-transform: uppercase;
  }

  /* back */
  .back-artwork {
    position: absolute; left: 0; top: 0;
    width: 280px; height: 180px;
  }
  .contact-person {
    position: absolute; right: 40px; top: 78px; text-align: right;
  }
  .person-name {
    font-weight: 700; font-size: 22px; letter-spacing: 1px;
    color: var(--silver); text-transform: uppercase;
  }
  .person-role { font-size: 15px; color: var(--silver-soft); }
  .contact-list {
    position: absolute; right: 40px; top: 168px;
    list-style: none; text-align: right;
    font-size: 13.5px; line-height: 17px; color: var(--silver);
  }
  .back-brand {
    position: absolute; left: 150px; bottom: 22px;
  }
  .back-brand .brand-name { color: var(--silver); font-size: 40px; }
  .back-brand .brand-tagline { color: var(--silver-soft); font-size: 11px; margin-top: 4px; }
</style>
</head>
<body>
  <section class="card card--front" aria-label="Business card front">
    <div class="front-pattern" role="img" aria-label="Faint embossed pattern of car outlines"></div>
    <div class="front-brand">
      <div class="brand-row">
        <span class="brand-dot"></span>
        <span class="brand-name">Apex Haul</span>
      </div>
      <span class="brand-tagline">The Auto Transport Professionals</span>
    </div>
  </section>

  <section class="card card--back" aria-label="Business card back">
    <svg class="back-artwork" viewBox="0 0 280 180" role="img" aria-label="Large glossy grey brand swoosh decoration">
      <defs>
        <linearGradient id="artFill" x1="0" y1="0" x2="1" y2="1">
          <stop offset="0" stop-color="var(--swoosh-light)"/>
          <stop offset="1" stop-color="var(--swoosh-dark)" stop-opacity="0"/>
        </linearGradient>
      </defs>
      <rect width="280" height="180" fill="url(#artFill)"/>
    </svg>

    <div class="contact-person">
      <div class="person-name">Dean Morrow</div>
      <div class="person-role">Dispatcher</div>
    </div>

    <ul class="contact-list">
      <li>(P) 555-201-0148</li>
      <li>(m) 555-201-0172</li>
      <li>apexhaulco@mail.com</li>
      <li>www.apexhaulco.com</li>
    </ul>

    <div class="back-brand">
      <div class="brand-name">Apex Haul</div>
      <div class="brand-tagline">The Auto Transport Professionals</div>
    </div>
  </section>
</body>
</html>
```